RW Framewell Inc Business cards

We need business cards using our existing logo but slightly modified. Right now the logo says RW Loadbearing Masonry. We want to keep the RW part of the design, but replace the Structural Concrete portion with "FRAMEWELL". Please see the attached file.
Ideally this would be a blank template so we can add Different Names, titles, and phone numbers later.
On the one side we want only the logo and on the other side the detail. I'm attaching an example for you to see.
Please reach out with any other questions. Our address and other details will be given out once we find a design we like.

Target Market(s)

Construction Industry

```html
<!DOCTYPE html>
<html lang="en">
<head>
<meta charset="utf-8">
<title>RW Framewell Inc – Business Cards</title>
<link rel="stylesheet" href="https://fonts.googleapis.com/css2?family=Michroma&family=Open+Sans:wght@400&display=swap">
<style>
  :root {
    --bg: #1f1f1f;
    --card-blue: #0f75bc;
    --card-grey: #808184;
    --name-light: #e4e6e8;
    --text-white: #ffffff;
  }
  * { margin: 0; padding: 0; box-sizing: border-box; }
  html, body { width: 1200px; height: 900px; overflow: hidden; }
  body {
    background: var(--bg);
    position: relative;
    font-family: "Open Sans", Arial, sans-serif;
  }
  .card {
    position: absolute;
    left: 280px;
    width: 640px;
    height: 366px;
    box-shadow: 0 10px 30px rgba(0,0,0,.5);
  }
  .card--front { top: 60px; background: var(--card-blue); }
  .card--back  { top: 470px; background: var(--card-grey); color: var(--text-white); }

  .company-name {
    display: flex;
    align-items: center;
    font-family: "Open Sans", Arial, sans-serif;
    font-weight: 400;
    line-height: 1;
    white-space: nowrap;
  }
  .company-name__square { flex: none; }

  .company-name--front {
    position: absolute;
    left: 0; right: 0; top: 50%;
    transform: translateY(-50%);
    justify-content: center;
    gap: 16px;
    font-size: 44px;
    color: var(--name-light);
  }
  .company-name--front .company-name__square {
    width: 30px; height: 30px;
    background: var(--name-light);
  }

  .company-name--back {
    position: absolute;
    left: 20px; top: 164px;
    width: 280px;
    justify-content: center;
    gap: 12px;
    font-size: 30px;
    color: var(--text-white);
  }
  .company-name--back .company-name__square {
    width: 22px; height: 22px;
    background: var(--text-white);
  }

  .back-divider {
    position: absolute;
    left: 320px; top: 70px;
    width: 2px; height: 230px;
    background: var(--text-white);
  }
  .details {
    position: absolute;
    left: 350px; top: 72px;
  }
  .details__name {
    font-family: "Michroma", Arial, sans-serif;
    font-size: 21px;
    letter-spacing: 1px;
    line-height: 1.1;
  }
  .details__title { font-size: 18px; margin-bottom: 16px; }
  .contact { list-style: none; font-size: 19px; line-height: 27px; }
  .contact li { display: flex; align-items: center; gap: 10px; }
  .contact svg { width: 16px; height: 16px; flex: none; fill: none; stroke: var(--text-white); stroke-width: 1.6; }
  .address { margin-top: 16px; font-size: 19px; line-height: 24px; }
</style>
</head>
<body>
  <section class="card card--front" aria-label="Business card front">
    <div class="company-name company-name--front">
      <span class="company-name__square"></span>
      <span>RW Framewell</span>
    </div>
  </section>

  <section class="card card--back" aria-label="Business card back">
    <div class="company-name company-name--back">
      <span class="company-name__square"></span>
      <span>RW Framewell</span>
    </div>
    <div class="back-divider"></div>
    <div class="details">
      <div class="details__name">ALEX CARTER</div>
      <div class="details__title">Chief Officer</div>
      <ul class="contact">
        <li>
          <svg viewBox="0 0 16 16"><path d="M3 2l3 0 1 3-2 1.5a8 8 0 0 0 4.5 4.5L11 9l3 1v3a1 1 0 0 1-1 1A11 11 0 0 1 2 3a1 1 0 0 1 1-1z"/></svg>
          +00 8 38 00 00
        </li>
        <li>
          <svg viewBox="0 0 16 16"><rect x="4" y="1.5" width="8" height="13" rx="1.2"/><line x1="7" y1="12" x2="9" y2="12"/></svg>
          +00 0 90 00 00
        </li>
        <li>
          <svg viewBox="0 0 16 16"><rect x="1.5" y="3.5" width="13" height="9"/><polyline points="1.5,3.5 8,9 14.5,3.5"/></svg>
          info@rwframewell.com
        </li>
        <li>
          <svg viewBox="0 0 16 16"><circle cx="8" cy="8" r="6.5"/><ellipse cx="8" cy="8" rx="3" ry="6.5"/><line x1="1.5" y1="8" x2="14.5" y2="8"/></svg>
          www.rwframewell.com
        </li>
      </ul>
      <p class="address">Your address line here<br>Country/ State</p>
    </div>
  </section>
</body>
</html>
```